Building company buisness cards

We are looking for a sharp modern new look for our business cards.
We are a New Zealand based company that specialises in house and land packages.
We have attached a photo of the current logo and would like to see if it can be improved somehow if needed.
We are open to any colours but we have chosen green at this stage.
Feel free to change the font and make the logo smarter looking.
Play with the colours and see what looks best.

We want a card that looks so good know one will want to throw it away!

Target Market(s)

Home buyers

Industry/Entity Type

Building

Contact Information for Business Card

Derek Tolvane
0217394062
dtolvane@quillmarkhomesteads.co.nz
quillmarkhomesteads.co.nz

Font styles to use
Serif
Sans Serif

Colors

Designer to choose colors to be used in the design.

Requirements
Must have
• Logo and company name on one side, details on the other side
Nice to have
• Color codes for the original green are HEX #4a8028, RGB(74,128,40), CMYK(42,0,69,50)
• Round corners, Raised and/or spot UV

```html
<!DOCTYPE html>
<html lang="en">
<head>
<meta charset="utf-8">
<title>Quillmark Homesteads – Business Cards</title>
<link rel="stylesheet" href="https://fonts.googleapis.com/css2?family=Montserrat:wght@500;800&family=Roboto:wght@400&display=swap">
<style>
  :root {
    --brand-green: #5e8243;
    --paper: #ffffff;
    --ink: #1e1e1e;
    --rule: #555555;
    --backdrop: #e6e1d8;
  }
  * { margin: 0; padding: 0; box-sizing: border-box; }
  html, body {
    width: 1200px; height: 1200px; overflow: hidden;
    background: var(--backdrop);
  }
  .canvas { position: relative; width: 1200px; height: 1200px; }

  .card { position: absolute; width: 745px; height: 425px; }
  .card--front { left: 229px; top: 147px; background: var(--brand-green); }
  .card--back  { left: 227px; top: 640px; background: var(--paper); }

  .wordmark {
    position: absolute;
    font-family: "Montserrat", sans-serif;
    font-weight: 800;
    line-height: 0.95;
    letter-spacing: -0.5px;
  }
  .wordmark__dot {
    display: block; border-radius: 50%;
  }

  .wordmark--front {
    left: 0; right: 0; top: 150px;
    display: flex; align-items: center; justify-content: center; gap: 18px;
    color: var(--paper);
  }
  .wordmark--front .wordmark__dot { width: 46px; height: 46px; background: var(--paper); }
  .wordmark--front .wordmark__text { font-size: 48px; }
  .wordmark--front .wordmark__line--small { font-size: 32px; display: block; }

  .wordmark--back {
    left: 20px; width: 295px; top: 160px;
    text-align: center; color: var(--brand-green);
  }
  .wordmark--back .wordmark__dot {
    width: 34px; height: 34px; background: var(--brand-green);
    margin: 0 auto 14px;
  }
  .wordmark--back .wordmark__line--small { display: block; font-size: 26px; }
  .wordmark--back .wordmark__line--large { display: block; font-size: 32px; }

  .divider {
    position: absolute; left: 334px; width: 1.5px; background: var(--rule);
  }
  .divider--name { top: 144px; height: 46px; }
  .divider--contact { top: 213px; height: 68px; }

  .person { position: absolute; left: 358px; top: 143px; }
  .person__name {
    font-family: "Montserrat", sans-serif; font-weight: 500;
    font-size: 28px; color: var(--brand-green); letter-spacing: 0.3px;
    line-height: 1;
  }
  .person__title {
    font-family: "Roboto", sans-serif; font-size: 16px; color: var(--ink);
    margin-top: 6px;
  }

  .contact-list { position: absolute; left: 358px; top: 210px; list-style: none; }
  .contact-list__item {
    display: flex; align-items: center; height: 26px;
    font-family: "Roboto", sans-serif; font-size: 17px; color: var(--ink);
    letter-spacing: 0.3px;
  }
  .contact-list__icon { width: 14px; height: 14px; margin-right: 14px; fill: var(--brand-green); }
</style>
</head>
<body>
<main class="canvas">

  <section class="card card--front" aria-label="Card front">
    <div class="wordmark wordmark--front">
      <span class="wordmark__dot"></span>
      <span class="wordmark__text">
        <span class="wordmark__line--small">quillmark</span>
        plans.
      </span>
    </div>
  </section>

  <section class="card card--back" aria-label="Card back">
    <div class="wordmark wordmark--back">
      <span class="wordmark__dot"></span>
      <span class="wordmark__line--small">quillmark</span>
      <span class="wordmark__line--large">homesteads.</span>
    </div>

    <span class="divider divider--name"></span>
    <span class="divider divider--contact"></span>

    <div class="person">
      <p class="person__name">DEREK TOLVANE</p>
      <p class="person__title">Founder &amp; CEO</p>
    </div>

    <ul class="contact-list">
      <li class="contact-list__item">
        <svg class="contact-list__icon" viewBox="0 0 24 24" aria-hidden="true"><path d="M6.6 10.8a15 15 0 0 0 6.6 6.6l2.2-2.2a1 1 0 0 1 1-.25 11.4 11.4 0 0 0 3.6.6 1 1 0 0 1 1 1V20a1 1 0 0 1-1 1A17 17 0 0 1 3 4a1 1 0 0 1 1-1h3.5a1 1 0 0 1 1 1c0 1.25.2 2.45.6 3.6a1 1 0 0 1-.25 1z"/></svg>
        0217394062
      </li>
      <li class="contact-list__item">
        <svg class="contact-list__icon" viewBox="0 0 24 24" aria-hidden="true"><path d="M2 5h20v2l-10 6L2 7z"/><path d="M2 9l10 6 10-6v10H2z"/></svg>
        dtolvane@quillmarkhomesteads.co.nz
      </li>
      <li class="contact-list__item">
        <svg class="contact-list__icon" viewBox="0 0 24 24" aria-hidden="true"><circle cx="12" cy="12" r="10" fill="none" stroke="#5e8243" stroke-width="2"/><ellipse cx="12" cy="12" rx="4.5" ry="10" fill="none" stroke="#5e8243" stroke-width="1.6"/><path d="M2 12h20M4 7h16M4 17h16" stroke="#5e8243" stroke-width="1.6" fill="none"/></svg>
        www.quillmarkhomesteads.co.nz
      </li>
    </ul>
  </section>

</main>
</body>
</html>
```